Copperleaf Roofing Business Card

This is my current business card. But I’d like to make some changes. Somewhere on the card I’d like to list some of the services we offer. Maybe on the back? But I’d still like to keep the red. White and black modern look.

-residential & commercial roofing
-Roof Repairs & Maintenance
-Storm Damage & Insurance Claims specialist
-Christmas Lights and permanent Christmas lights
Fencing. Windows. Gutters. Siding. Sheetrock, painting.

```html
<!DOCTYPE html>
<html lang="en">
<head>
<meta charset="UTF-8">
<title>Copperleaf Roofing Co. – Business Card</title>
<link href="https://fonts.googleapis.com/css2?family=Michroma&family=Arimo:wght@700&family=Lato:wght@400&display=swap" rel="stylesheet">
<style>
  :root {
    --stage: #3b3b3d;
    --red: #d8202a;
    --red-deep: #8e0f14;
    --red-dark: #5e0a0d;
    --black: #050505;
    --white: #ffffff;
    --grey-text: #e9e9e9;
  }
  * { box-sizing: border-box; margin: 0; padding: 0; }
  html, body {
    width: 1200px; height: 694px; overflow: hidden;
    background: var(--stage);
  }
  .canvas {
    position: relative; width: 1200px; height: 694px;
  }
  .card {
    position: absolute; top: 192px;
    width: 540px; height: 310px;
    border-radius: 18px; overflow: hidden;
    box-shadow: 0 14px 30px rgba(0,0,0,.45);
  }
  .card--front { left: 30px; }
  .card--back { left: 630px; background: var(--black); }

  /* front */
  .tartan-field {
    position: absolute; inset: 0;
    background:
      linear-gradient(135deg, var(--red-deep) 0%, var(--red) 38%, var(--red-dark) 62%, var(--red) 82%, var(--red-deep) 100%);
  }
  .front-content {
    position: relative; height: 100%;
    display: flex; flex-direction: column; align-items: center;
    padding-top: 26px;
  }
  .brand-mark {
    width: 96px; height: 96px; border-radius: 50%;
    background: var(--red); border: 4px solid var(--white);
    box-shadow: 0 0 0 3px var(--black);
  }
  .brand-name {
    font-family: "Michroma", sans-serif; color: var(--white);
    text-align: center; line-height: 1.05; margin-top: 10px;
  }
  .brand-name__main { display: block; font-size: 31px; letter-spacing: 1px; }
  .brand-name__sub { display: block; font-size: 19px; letter-spacing: 1px; margin-top: 2px; }
  .services {
    margin-top: 14px; padding: 0 26px;
    font-family: "Arimo", sans-serif; font-weight: 700;
    font-size: 11.5px; line-height: 1.45; color: var(--white);
    text-align: center;
  }

  /* back */
  .tartan-band {
    position: absolute; left: 0; right: 0; bottom: 0; height: 30px;
    background: linear-gradient(90deg, var(--red-deep), var(--red) 30%, var(--red-dark) 55%, var(--red) 80%, var(--red-deep));
  }
  .back-brand {
    position: absolute; top: 34px; left: 0; right: 0;
    display: flex; flex-direction: column; align-items: center;
  }
  .back-brand .brand-mark { width: 84px; height: 84px; }
  .back-brand .brand-name__main { font-size: 27px; }
  .back-brand .brand-name__sub { font-size: 17px; }
  .back-details {
    position: absolute; top: 200px; left: 0; right: 0;
    display: flex; justify-content: center; align-items: center; gap: 18px;
  }
  .person { text-align: right; }
  .person__name {
    font-family: "Michroma", sans-serif; color: var(--red);
    font-size: 15px; letter-spacing: .5px;
  }
  .person__title {
    font-family: "Lato", sans-serif; color: var(--white);
    font-size: 13px; margin-top: 3px;
  }
  .divider { width: 2px; height: 58px; background: var(--red); }
  .contact-list { list-style: none; }
  .contact-list li {
    display: flex; align-items: center; gap: 8px;
    font-family: "Lato", sans-serif; color: var(--grey-text);
    font-size: 12.5px; line-height: 19px;
  }
  .contact-list svg { width: 13px; height: 13px; flex: none; }
</style>
</head>
<body>
<div class="canvas">

  <section class="card card--front">
    <div class="tartan-field" role="img" aria-label="Red, black and white tartan plaid pattern filling the card"></div>
    <div class="front-content">
      <div class="brand-mark"></div>
      <h1 class="brand-name">
        <span class="brand-name__main">COPPERLEAF</span>
        <span class="brand-name__sub">ROOFING CO.</span>
      </h1>
      <p class="services">
        • Residential &amp; commercial roofing • Roof Repairs &amp; Maintenance • Storm Damage &amp;
        Insurance Claims specialist • Christmas Lights and permanent Christmas light
        • Fencing • Windows • Siding • Sheetrock • Painting
      </p>
    </div>
  </section>

  <section class="card card--back">
    <div class="back-brand">
      <div class="brand-mark"></div>
      <h2 class="brand-name">
        <span class="brand-name__main">COPPERLEAF</span>
        <span class="brand-name__sub">ROOFING CO.</span>
      </h2>
    </div>
    <div class="back-details">
      <div class="person">
        <p class="person__name">DANA WHITFIELD</p>
        <p class="person__title">Owner</p>
      </div>
      <div class="divider"></div>
      <ul class="contact-list">
        <li>
          <svg viewBox="0 0 24 24" aria-hidden="true"><path fill="#d8202a" d="M6.6 10.8a15.1 15.1 0 0 0 6.6 6.6l2.2-2.2a1 1 0 0 1 1-.25 11.4 11.4 0 0 0 3.6.57 1 1 0 0 1 1 1V20a1 1 0 0 1-1 1A17 17 0 0 1 3 4a1 1 0 0 1 1-1h3.5a1 1 0 0 1 1 1c0 1.25.2 2.45.57 3.6a1 1 0 0 1-.25 1z"/></svg>
          555-210-4873
        </li>
        <li>
          <svg viewBox="0 0 24 24" aria-hidden="true"><path fill="#d8202a" d="M2 5h20v14H2z"/><path fill="none" stroke="#050505" stroke-width="2" d="M2 5l10 8 10-8"/></svg>
          dana@copperleafroofing.co
        </li>
        <li>
          <svg viewBox="0 0 24 24" aria-hidden="true"><circle cx="12" cy="12" r="10" fill="none" stroke="#d8202a" stroke-width="2"/><path fill="none" stroke="#d8202a" stroke-width="2" d="M2 12h20M12 2c3 3 3 17 0 20M12 2c-3 3-3 17 0 20"/></svg>
          www.copperleafroofing.co
        </li>
      </ul>
    </div>
    <div class="tartan-band" role="img" aria-label="Strip of red, black and white tartan plaid along the bottom edge"></div>
  </section>

</div>
</body>
</html>
```